Updated DJ business Card showing other businesses

DJ Talbo offers professional mobile dj services including DJ. MC. Karaoke.
Silent Disco (will attach logo)
I also offer a 360 Photo Booth.

Contact info:
(405) 555-0147
mark.fenstell@pelimail.com
Social Media @DJTalboOKC

```html
<!DOCTYPE html>
<html lang="en">
<head>
<meta charset="utf-8">
<title>DJ Talbo – Business Card</title>
<link rel="stylesheet" href="https://fonts.googleapis.com/css2?family=Poppins:wght@400;800&family=Oswald:wght@600&display=swap">
<style>
  :root {
    --ink: #0b0b0b;
    --paper: #ffffff;
    --accent: #ef1a45;
    --accent-dim: #c41d43;
    --backdrop: #3a3a3a;
    --text-soft: #2a2a2a;
  }
  * { box-sizing: border-box; margin: 0; padding: 0; }
  html, body { width: 1200px; height: 1200px; overflow: hidden; }
  body {
    background: var(--backdrop);
    font-family: "Poppins", sans-serif;
    position: relative;
  }
  .card {
    position: absolute;
    left: 120px;
    width: 960px;
    height: 540px;
    border-radius: 44px;
    overflow: hidden;
  }
  .card--front { top: 40px; background: var(--paper); }
  .card--back { top: 620px; background: var(--ink); }

  .front-mascot-art {
    position: absolute; left: 0; top: 0; width: 960px; height: 540px;
  }
  .front-info {
    position: absolute;
    left: 450px;
    top: 110px;
    width: 460px;
  }
  .wordmark {
    font-family: "Poppins", sans-serif;
    font-weight: 800;
    letter-spacing: -1px;
    line-height: 1;
    white-space: nowrap;
  }
  .front-info .wordmark { font-size: 76px; color: var(--ink); }
  .contact-list { list-style: none; margin-top: 22px; }
  .contact-item {
    display: flex; align-items: center; gap: 12px;
    font-size: 25px; color: var(--text-soft); line-height: 1.55;
    white-space: nowrap;
  }
  .contact-icon { width: 24px; height: 24px; flex: none; }
  .social-dot {
    width: 22px; height: 22px; border-radius: 50%;
    border: 3px solid var(--accent); flex: none;
  }
  .services {
    position: absolute;
    right: 50px;
    bottom: 56px;
    text-align: right;
    font-family: "Oswald", sans-serif;
    font-weight: 600;
    text-transform: uppercase;
    color: var(--ink);
    font-size: 27px;
    line-height: 1.25;
    white-space: nowrap;
  }
  .services .sep { color: var(--accent); padding: 0 6px; }

  .back-brand {
    position: absolute;
    left: 0; right: 0; top: 140px;
    text-align: center;
  }
  .back-brand .wordmark { font-size: 130px; color: var(--paper); }
  .partner-name {
    margin-top: 26px;
    font-family: "Poppins", sans-serif;
    font-weight: 800;
    font-size: 36px;
    color: var(--paper);
    text-transform: uppercase;
    letter-spacing: 2px;
  }
  .level-bars { position: absolute; left: 0; bottom: 0; width: 100%; height: 200px; }
  .level-bars rect { fill: var(--accent-dim); }
</style>
</head>
<body>

<section class="card card--front">
  <svg class="front-mascot-art" viewBox="0 0 960 540" role="img" aria-label="Large black rhino mascot illustration cropped at the left of the card">
    <path d="M0 190 C110 170 220 190 285 250 C325 290 350 390 400 540 L0 540 Z" fill="var(--ink)"/>
  </svg>

  <div class="front-info">
    <div class="wordmark">DJ Talbo</div>
    <ul class="contact-list">
      <li class="contact-item">
        <svg class="contact-icon" viewBox="0 0 24 24"><path fill="var(--accent)" d="M6.6 10.8a15 15 0 0 0 6.6 6.6l2.2-2.2a1 1 0 0 1 1-.25 11.4 11.4 0 0 0 3.6.57 1 1 0 0 1 1 1V20a1 1 0 0 1-1 1A17 17 0 0 1 3 4a1 1 0 0 1 1-1h3.5a1 1 0 0 1 1 1c0 1.25.2 2.45.57 3.57a1 1 0 0 1-.25 1z"/></svg>
        (405) 555-0147
      </li>
      <li class="contact-item">
        <svg class="contact-icon" viewBox="0 0 24 24"><rect x="2" y="5" width="20" height="14" rx="1" fill="var(--accent)"/><path d="M2.5 6l9.5 7 9.5-7" stroke="var(--paper)" stroke-width="1.6" fill="none"/></svg>
        mark.fenstell@pelimail.com
      </li>
      <li class="contact-item">
        <span class="social-dot"></span>
        @DJTalboOKC
      </li>
    </ul>
  </div>

  <div class="services">
    <div>Mobile DJ Services</div>
    <div>DJ<span class="sep">•</span>MC<span class="sep">•</span>Karaoke<span class="sep">•</span>360 Photo Booth</div>
  </div>
</section>

<section class="card card--back">
  <div class="back-brand">
    <div class="wordmark">DJ Talbo</div>
    <div class="partner-name">Silent Disco</div>
  </div>
  <svg class="level-bars" viewBox="0 0 960 200" preserveAspectRatio="none" aria-hidden="true">
    <rect x="20" y="170" width="14" height="30"/><rect x="50" y="150" width="14" height="50"/>
    <rect x="80" y="160" width="14" height="40"/><rect x="110" y="120" width="14" height="80"/>
    <rect x="140" y="165" width="14" height="35"/><rect x="170" y="140" width="14" height="60"/>
    <rect x="200" y="155" width="14" height="45"/><rect x="230" y="100" width="14" height="100"/>
    <rect x="260" y="150" width="14" height="50"/><rect x="290" y="130" width="14" height="70"/>
    <rect x="320" y="160" width="14" height="40"/><rect x="350" y="110" width="14" height="90"/>
    <rect x="380" y="145" width="14" height="55"/><rect x="410" y="125" width="14" height="75"/>
    <rect x="440" y="90" width="14" height="110"/><rect x="470" y="140" width="14" height="60"/>
    <rect x="500" y="115" width="14" height="85"/><rect x="530" y="150" width="14" height="50"/>
    <rect x="560" y="100" width="14" height="100"/><rect x="590" y="130" width="14" height="70"/>
    <rect x="620" y="80" width="14" height="120"/><rect x="650" y="140" width="14" height="60"/>
    <rect x="680" y="110" width="14" height="90"/><rect x="710" y="150" width="14" height="50"/>
    <rect x="740" y="95" width="14" height="105"/><rect x="770" y="130" width="14" height="70"/>
    <rect x="800" y="70" width="14" height="130"/><rect x="830" y="145" width="14" height="55"/>
    <rect x="860" y="105" width="14" height="95"/><rect x="890" y="160" width="14" height="40"/>
    <rect x="920" y="120" width="14" height="80"/>
  </svg>
</section>

</body>
</html>
```